Business Card Design

We need a business card designed for our new company. Prefer a black card with white logo & writing.

Contact Information for Business Card

Ted Galloway, address: 7-4812 Fernhollow Road, Abbotsford, BC, V3K 8R2, Office Phone: 604-712-3390, Cell: 604-947-2164, Email: ted@resinworkshub.ca

Colors

Designer to choose only greyscale colors for use in the design.

```html
<!DOCTYPE html>
<html lang="en">
<head>
<meta charset="UTF-8">
<title>Resin Works Hub – Business Card</title>
<link rel="stylesheet" href="https://fonts.googleapis.com/css2?family=Montserrat:wght@400;600;700;800&display=swap">
<style>
  :root {
    --page-bg: #e6e4e1;
    --card-bg: #212121;
    --card-bg-deep: #151515;
    --pattern-light: #3a3a3a;
    --pattern-dark: #0c0c0c;
    --ink: #ffffff;
    --ink-soft: #e4e4e4;
  }
  * { margin: 0; padding: 0; box-sizing: border-box; }
  html, body { width: 900px; height: 1200px; overflow: hidden; }
  body {
    background: var(--page-bg);
    font-family: "Montserrat", sans-serif;
    color: var(--ink);
    position: relative;
  }
  .card {
    position: absolute;
    left: 80px;
    width: 742px;
    height: 442px;
    border-radius: 22px;
    background: var(--card-bg);
    overflow: hidden;
  }
  .card-front { top: 130px; }
  .card-back { top: 638px; height: 440px; }

  .brand-name {
    position: absolute;
    left: 236px;
    top: 333px;
    transform: translate(-50%, -50%);
    position: absolute;
    font-weight: 800;
    font-size: 24px;
    line-height: 1.05;
    letter-spacing: 0.5px;
    text-align: center;
    color: var(--ink);
    white-space: nowrap;
  }
  .card-front .brand-name { left: 260px; top: 223px; }

  .divider {
    position: absolute;
    left: 370px;
    top: 135px;
    width: 3px;
    height: 176px;
    background: var(--ink);
  }
  .identity { position: absolute; left: 392px; top: 128px; }
  .person-name { font-weight: 700; font-size: 25px; line-height: 1.2; }
  .person-role { font-size: 15px; font-weight: 400; margin-top: 4px; color: var(--ink-soft); }

  .contact-list {
    position: absolute;
    left: 392px;
    top: 208px;
    list-style: none;
  }
  .contact-item {
    display: flex;
    align-items: center;
    height: 27px;
    font-size: 15.5px;
    color: var(--ink-soft);
  }
  .contact-item:nth-child(2) { margin-top: 3px; }
  .contact-icon { width: 16px; height: 16px; margin-right: 12px; fill: var(--ink); flex: none; }

  .address {
    position: absolute;
    left: 0; right: 0;
    top: 375px;
    text-align: center;
    padding-left: 50px;
    font-size: 16px;
    color: var(--ink-soft);
  }

  .pattern-field {
    position: absolute;
    inset: 0;
    background: linear-gradient(120deg, var(--pattern-light) 0%, var(--card-bg) 35%, var(--pattern-dark) 70%, var(--card-bg-deep) 100%);
  }
  .card-back .brand-name { left: 553px; top: 329px; font-size: 18px; }
</style>
</head>
<body>

<section class="card card-front" aria-label="Business card front">
  <div class="brand-name">RESIN WORKS<br>HUB</div>
  <div class="divider"></div>
  <div class="identity">
    <h1 class="person-name">Ted Galloway</h1>
    <p class="person-role">owner</p>
  </div>
  <ul class="contact-list">
    <li class="contact-item">
      <svg class="contact-icon" viewBox="0 0 24 24"><path d="M6.6 10.8a15.1 15.1 0 0 0 6.6 6.6l2.2-2.2c.3-.3.7-.4 1-.2 1.1.4 2.3.6 3.6.6.6 0 1 .4 1 1V20c0 .6-.4 1-1 1A17 17 0 0 1 3 4c0-.6.4-1 1-1h3.5c.6 0 1 .4 1 1 0 1.3.2 2.5.6 3.6.1.3 0 .7-.2 1l-2.3 2.2z"/></svg>
      604-712-3390
    </li>
    <li class="contact-item">
      <svg class="contact-icon" viewBox="0 0 24 24"><path d="M7 1h10a2 2 0 0 1 2 2v18a2 2 0 0 1-2 2H7a2 2 0 0 1-2-2V3a2 2 0 0 1 2-2zm0 3v14h10V4H7zm5 15.5a1.2 1.2 0 1 0 0 2.4 1.2 1.2 0 0 0 0-2.4z"/></svg>
      604-947-2164
    </li>
    <li class="contact-item">
      <svg class="contact-icon" viewBox="0 0 24 24"><path d="M3 5h18v14H3V5zm2 2v.5l7 4.5 7-4.5V7H5zm0 2.9V17h14V9.9l-7 4.5-7-4.5z"/></svg>
      ted@resinworkshub.ca
    </li>
    <li class="contact-item">
      <svg class="contact-icon" viewBox="0 0 24 24"><path d="M12 2a10 10 0 1 0 0 20 10 10 0 0 0 0-20zm-1 17.9A8 8 0 0 1 4.2 10.2L9 15v1a2 2 0 0 0 2 2v1.9zm6.9-2.5A2 2 0 0 0 16 16h-1v-3a1 1 0 0 0-1-1H8v-2h2a1 1 0 0 0 1-1V7h2a2 2 0 0 0 2-2v-.4a8 8 0 0 1 2.9 12.8z"/></svg>
      www.resinworkshub.ca
    </li>
  </ul>
  <p class="address">7-4812 Fernhollow Road, Abbotsford, BC, V3K 8R2</p>
</section>

<section class="card card-back" aria-label="Business card back">
  <div class="pattern-field" role="img" aria-label="Repeating tone-on-tone brand pattern fading from grey to black"></div>
  <div class="brand-name">RESIN WORKS<br>HUB</div>
</section>

</body>
</html>
```